Animal Eye Clinic needs a Business card

We are a new veterinary ophthalmology practice (Ridgeline Pet Vision Care) and we need a business card designed. We only see animal eyes - we are not a regular veterinary clinic. We already have a logo. We are looking for a professional, good looking business card to hand out to our clients. We are looking for something simple but professional and contemporary. Our logo is likely the only picture/graphic that needs to be on the card.
Updates

Contact Information for Business Card

Delia Vossman, BSc, DVM, MSc, DipACVO
Veterinary Ophthalmologist

Phone: 250.418.3927
Email: ridgelinepetvisioncare@mailbox-example.net
Website: ridgelinepetvisioncare-example.net
Address: 1874 Thornbury Rd
Kelowna, BC, V1X 4M9

Colors

Designer to choose colors to be used in the design.

Requirements
Must have
• Our logo (attached)

```html
<!DOCTYPE html>
<html lang="en">
<head>
<meta charset="utf-8">
<title>Ridgeline Pet Vision Care – Business Card</title>
<link rel="stylesheet" href="https://fonts.googleapis.com/css2?family=Libre+Franklin:wght@400;600;800&display=swap">
<style>
  :root {
    --backdrop: #1c1c1e;
    --card: #231f20;
    --teal: #1596a8;
    --white: #f4f4f4;
    --grey: #9a9a9a;
  }
  * { margin: 0; padding: 0; box-sizing: border-box; }
  html, body { width: 1200px; height: 900px; overflow: hidden; }
  body {
    background: var(--backdrop);
    font-family: "Libre Franklin", Arial, sans-serif;
    position: relative;
  }
  .card {
    position: absolute;
    width: 520px;
    height: 300px;
    background: var(--card);
    overflow: hidden;
    box-shadow: 0 10px 28px rgba(0,0,0,.55);
  }
  .card--front { left: 90px; top: 110px; }
  .card--back { left: 590px; top: 490px; }
  .card__band { position: absolute; left: 0; top: 0; width: 520px; height: 300px; }
  .brand {
    position: absolute;
    display: flex;
    align-items: center;
    gap: 10px;
    color: var(--teal);
    font-weight: 800;
    text-transform: uppercase;
    letter-spacing: .02em;
    line-height: 1;
    z-index: 1;
  }
  .brand__dot {
    width: 34px; height: 34px;
    border-radius: 50%;
    background: var(--teal);
    flex: none;
  }
  .card--front .brand { left: 150px; top: 70px; font-size: 21px; }
  .card--back .brand { left: 34px; top: 132px; font-size: 17px; }
  .card--back .brand__dot { width: 28px; height: 28px; }
  .brand__name span { display: block; }
  .band-text {
    fill: var(--white);
    font-family: "Libre Franklin", Arial, sans-serif;
    font-size: 13px;
    font-weight: 600;
  }
  .person {
    position: absolute;
    right: 40px;
    top: 34px;
    text-align: right;
  }
  .person__name {
    color: var(--teal);
    font-size: 24px;
    font-weight: 800;
    text-transform: uppercase;
    letter-spacing: .02em;
  }
  .person__creds, .person__title {
    color: var(--white);
    font-size: 12px;
    margin-top: 3px;
  }
  .contact {
    position: absolute;
    left: 34px;
    top: 192px;
    list-style: none;
    color: var(--white);
    font-size: 12.5px;
    font-weight: 600;
    z-index: 1;
  }
  .contact__row { display: flex; gap: 16px; margin-bottom: 7px; }
  .contact__item { display: flex; align-items: center; gap: 6px; }
  .contact__icon { width: 14px; height: 14px; flex: none; }
</style>
</head>
<body>

<section class="card card--front" aria-label="Business card front">
  <svg class="card__band" viewBox="0 0 520 300">
    <path d="M30,300 Q200,168 520,128 L520,150 Q270,190 120,300 Z" fill="var(--teal)"/>
    <path id="front-curve" d="M75,300 Q232,180 520,139" fill="none"/>
    <text class="band-text" dy="4"><textPath href="#front-curve" startOffset="40%">ridgelinepetvisioncare-example.net</textPath></text>
  </svg>
  <div class="brand">
    <span class="brand__dot"></span>
    <span class="brand__name"><span>Ridgeline</span><span>Pet Vision Care</span></span>
  </div>
</section>

<section class="card card--back" aria-label="Business card back">
  <svg class="card__band" viewBox="0 0 520 300" aria-hidden="true">
    <path d="M210,300 Q370,228 520,215 L520,250 Q420,258 350,300 Z" fill="var(--teal)"/>
  </svg>
  <div class="person">
    <h1 class="person__name">Delia Vossman</h1>
    <p class="person__creds">BSc, DVM, MSc, DipACVO</p>
    <p class="person__title">Veterinary Ophthalmologist</p>
  </div>
  <div class="brand">
    <span class="brand__dot"></span>
    <span class="brand__name"><span>Ridgeline</span><span>Pet Vision Care</span></span>
  </div>
  <ul class="contact">
    <li class="contact__row">
      <span class="contact__item">
        <svg class="contact__icon" viewBox="0 0 14 14"><circle cx="7" cy="7" r="7" fill="var(--teal)"/><path d="M4.5,3.5 L6,3.5 L6.5,5.5 L5.6,6.2 Q6.3,7.8 7.8,8.4 L8.5,7.5 L10.5,8 L10.5,9.5 Q6,10 4.5,3.5 Z" fill="var(--card)"/></svg>
        250.418.3927
      </span>
      <span class="contact__item">
        <svg class="contact__icon" viewBox="0 0 14 14"><circle cx="7" cy="7" r="7" fill="var(--teal)"/><path d="M7,3 A2.6,2.6 0 0 1 9.6,5.6 Q9.6,7.6 7,11 Q4.4,7.6 4.4,5.6 A2.6,2.6 0 0 1 7,3 Z" fill="var(--card)"/><circle cx="7" cy="5.6" r="1" fill="var(--teal)"/></svg>
        1874 Thornbury Rd, Kelowna, BC, V1X 4M9
      </span>
    </li>
    <li class="contact__row">
      <span class="contact__item">
        <svg class="contact__icon" viewBox="0 0 14 14"><circle cx="7" cy="7" r="7" fill="var(--teal)"/><rect x="3.5" y="4.5" width="7" height="5" fill="var(--card)"/><path d="M3.5,4.5 L7,7.3 L10.5,4.5" fill="none" stroke="var(--teal)" stroke-width=".8"/></svg>
        ridgelinepetvisioncare@mailbox-example.net
      </span>
    </li>
  </ul>
</section>

</body>
</html>
```